Website for a health information tech company

I need a website for a new startup company, Velorim Health, Inc. that specializes in healthcare information technology. Velorim Health is a monitoring system that uses wearable sensors and predictive algorithms to detect when an elderly persons health is declining and triggers progressively higher levels of interventions.

The site needs to be very simple, elegant and initially will have minimal information as company and product is still under development and is in a stealth mode. I like the lumotreva.com website as it has a "single page" look and feel with sliding vertical sections. Ideally the sections would be "Home", "Technology", "Customers", "News", "About Us" and "Contact Us". The contact us should have a contact form that gets sent to an email address.

I have a couple of example sites that my site should take inspiration from (lumotreva.com and bixendale.com). I would like a WordPress backend so I can easily update content so the winning design should be easily importable or setup into Wordpress.

Target Market(s)

Investors, Customers (Doctors, Patients, Health Insurance companies, Hospital directors)

Industry/Entity Type

Healthcare

Requirements
Must have
• top horizontal menu that gets repeated on each vertical slide. Should have animated vertical slides. Must be viewable on any device (iPad, Android Tablets) correctly and must render correctly on different screen sizes. Must be viewable in all popular browsers. Must work well with touchscreen devices such as iPad, iPhone, Android tablets and phones.
Must have a content management system backend such as WordPress so I can edit/update content and in future add additional sections, images etc.

See attached company logo so colors must be complimentary to the logo colors. Feel free to use the logo colors as web site theme colors if it makes sense.
Nice to have
• Nice subtle textured background like linen or leather.
Should not have
• Not looking for traditional web site design with nav bars on left etc
Should not feel like a traditional web site where you click a link and another page loads. It must be animated slide into a different section. No flash or any other technology that requires plug ins.

```html
<!DOCTYPE html>
<html lang="en">
<head>
<meta charset="utf-8">
<title>Velorim Health — Home</title>
<link href="https://fonts.googleapis.com/css2?family=Arimo:wght@400;700&display=swap" rel="stylesheet">
<style>
  :root {
    --orange: #ec6a16;
    --orange-dark: #d9560b;
    --ink: #111111;
    --text: #222222;
    --muted: #555555;
    --grey: #8a8a8a;
    --header-bg: #fafafa;
    --hero-a: #e9ecef;
    --hero-b: #cfd6dd;
    --footer-bg: #ffffff;
    --button: #3a3a3a;
    --dot: #6b6b6b;
  }
  * { box-sizing: border-box; margin: 0; padding: 0; }
  html, body { width: 1200px; height: 801px; overflow: hidden; }
  body {
    position: relative;
    font-family: "Arimo", Arial, sans-serif;
    color: var(--text);
    background: var(--footer-bg);
  }

  /* Header */
  .site-header {
    position: absolute; left: 0; top: 0; width: 1200px; height: 143px;
    background: var(--header-bg);
    border-bottom: 1px solid #e4e4e4;
    z-index: 2;
  }
  .brand {
    position: absolute; left: 90px; top: 92px;
    display: flex; align-items: center; gap: 10px;
    font-size: 25px; font-weight: 400; color: var(--orange);
  }
  .brand-mark { width: 16px; height: 16px; background: var(--orange); }
  .account-links {
    position: absolute; right: 89px; top: 33px;
    font-size: 14px; font-weight: 700; color: var(--orange-dark);
    word-spacing: 6px;
  }
  .main-nav {
    position: absolute; right: 89px; top: 82px;
    display: flex; align-items: center; font-size: 15px; color: var(--ink);
  }
  .main-nav a { color: inherit; text-decoration: none; padding: 0 11px; line-height: 25px; }
  .main-nav .sep { font-size: 12px; color: #444; }
  .main-nav a.current { background: var(--orange); color: #fff; border-radius: 2px; }

  /* Hero */
  .hero {
    position: absolute; left: 0; top: 143px; width: 1200px; height: 522px;
  }
  .hero-photo {
    position: absolute; inset: 0;
    background: radial-gradient(ellipse at 70% 35%, #f1ede9 0%, var(--hero-a) 40%, var(--hero-b) 100%);
  }
  .hero-title {
    position: absolute; left: 114px; top: 177px;
    font-size: 22px; font-weight: 700; color: var(--orange);
  }
  .hero-copy {
    position: absolute; left: 114px; top: 215px; width: 471px;
    font-size: 14.4px; line-height: 23px; color: var(--ink); text-align: justify;
  }
  .hero-copy p + p { margin-top: 8px; }
  .btn-more {
    position: absolute; left: 115px; top: 375px; width: 117px; height: 40px;
    background: linear-gradient(#555, var(--button) 50%, #222);
    border-radius: 3px; color: #fff; font-size: 14.5px; font-weight: 700;
    display: flex; align-items: center; justify-content: center;
  }
  .slide-dots { position: absolute; left: 115px; top: 474px; display: flex; gap: 14px; }
  .slide-dots span {
    width: 19px; height: 19px; border-radius: 50%;
    background: var(--dot); border: 3px solid #fff;
  }
  .slide-dots span.active { background: var(--orange); }
  .device-showcase {
    position: absolute; left: 694px; top: 168px; width: 417px; height: 315px;
    background: linear-gradient(180deg, #3a3a3a 0%, #dfe6ee 12%, #c9d5e2 70%, #b9bcc0 100%);
    border-radius: 10px;
  }

  /* Footer */
  .site-footer { position: absolute; left: 0; top: 665px; width: 1200px; height: 136px; }
  .footer-nav { position: absolute; left: 90px; top: 20px; font-size: 13.5px; color: var(--muted); }
  .footer-nav a { color: inherit; text-decoration: none; }
  .footer-nav .sep { padding: 0 10px; }
  .copyright { position: absolute; left: 90px; top: 53px; font-size: 13px; color: var(--muted); word-spacing: 2px; }
  .social { position: absolute; left: 90px; top: 90px; display: flex; gap: 6px; }
  .social span { width: 25px; height: 25px; border-radius: 3px; background: #3b5a9a; }
  .social span + span { background: #3fb2e4; }
  .footer-brand {
    position: absolute; left: 730px; top: 60px;
    font-size: 19px; color: var(--grey);
  }
  .footer-tagline {
    position: absolute; left: 889px; top: 30px; width: 240px;
    font-size: 19.5px; line-height: 28px; color: var(--muted);
  }
</style>
</head>
<body>
  <header class="site-header">
    <div class="brand"><span class="brand-mark"></span>Velorim Health</div>
    <div class="account-links">REGISTER :: LOGIN</div>
    <nav class="main-nav">
      <a class="current" href="#">Home</a><span class="sep">::</span>
      <a href="#">Technology</a><span class="sep">::</span>
      <a href="#">Customers</a><span class="sep">::</span>
      <a href="#">About Us</a><span class="sep">::</span>
      <a href="#" style="padding-right:0">Contact Us</a>
    </nav>
  </header>

  <section class="hero">
    <div class="hero-photo" role="img" aria-label="Blurred photo of smiling medical staff in a hospital corridor"></div>
    <h1 class="hero-title">Welcome to Velorim Health</h1>
    <div class="hero-copy">
      <p>Velorim Health is a patent pending monitoring system that uses wearable sensorsand predictive algorithms to detect when anelderlypersons health is declining and triggers progressively higher levels of interventions.</p>
      <p>The goal is to allow an elderly person, who often has 2 or more chronic conditions, &nbsp;to age in place and stay independent as long as possible by the use of &nbsp;intelligent monitoring to deliver just in time care.</p>
    </div>
    <div class="btn-more">VIEW MORE</div>
    <div class="slide-dots"><span class="active"></span><span></span><span></span><span></span></div>
    <div class="device-showcase" role="img" aria-label="Desktop monitor and smartphone showing the monitoring dashboard with tables and bar charts"></div>
  </section>

  <footer class="site-footer">
    <nav class="footer-nav">
      <a href="#">Home</a><span class="sep">|</span><a href="#">Technology</a><span class="sep">|</span><a href="#">Customers</a><span class="sep">|</span><a href="#">About Us</a><span class="sep">|</span><a href="#">Contact Us</a>
    </nav>
    <div class="copyright">Copyright &copy; 2013 &nbsp; www.velorimhealth.com &nbsp; All rights reserved.</div>
    <div class="social"><span></span><span></span></div>
    <div class="footer-brand">Velorim Health</div>
    <p class="footer-tagline">Maecenas semlar sem, molestie sed faucibus eu, viverra eget ante...</p>
  </footer>
</body>
</html>
```